Bold, Modern, Clean "Kestrelwaymassage.com" website

Why we stand out?
We are a male and female mobile massage team. Our names are Paul and Lina. 
Kestrel Way is a Seattle based mobile massage service. Our massage is offered to the community with a goal of facilitating balance within each individual. We specialize in integrated Pain management, and sports/medical massage therapy. Every client's first assessment is attended by our male and female massage therapist team. Depending on the goals identified for an individual determines which therapist will be assigned to provide treatment, if not both.

Our passion...
Here at Kestrel Way, we have a great passion for Postural Resoration and how it is integrated into an individual's Massage treatment. We pride ourselves in being natural facilitators of healing, which takes the ego of the therapist out of the client's healing process. We strive to deliver the best massage possible by including modalities such as Neuromuscular, Myofascial release, spontaneous muscle release, postural restoration, orthopedic, and medical massage.

Our education...

We are both Graduates of Venmora, school of massage therapy. We have continuing education in medical massage, myofacial release, trigger point therapy, postural restoration, anatomy, and spontaneous muscle release. Lina is also a Certified Yoga Instructor, which amplifies her experience with flexibility and strength as it pertains to each individual. Paul's passion is Massage, stretching, and strength training to encourage postural restoration and realignment.

Our rates-

Our rates are $75/ 60 minutes, $95/ 90 minutes, and $120/ 120 minutes.

Education-
Both Lina and I worked as behavioral health professionals that specialized in life skills mentoring for youth who had experienced different types of trauma. This led us both to want to help others in a different environment, where individuals can be empowered to take responsibility over their own healing. To us, massage is a type of manipulation physical therapy, that encourages healing on many levels.

Advice to any massage client-
The most important thing to 'us', as Licenced providers is to get you on to our table to show you our skills. But a good therapist never forgets that it's not about what we do for you, but what we can facilitate for you. Your health and healing has nothing to do with us. It is yours, not ours. Identify what your goals are with any Therapist, and know what the end looks like. Progress should be tangible, such as range of motion, and decreased pain.

Lina and Paul at Kestrel Way are awesome! I recently had open heart surgery, and Lina worked on me to increase my range of motion while helping with the pinched nerve from my arm being in the same position for so long during my surgery. My wife drives a lot for work, and Paul has helped decrease her neck and lower back pain immensely. They are seriously the best therapists I have ever worked with. I would recommend them to anyone who needs anything from stress relief to a medical massage treatment. They are professional, up beat, easy going, and always on time. And, I love that they meet us where ever we like! We did a staycation recently, where they came to our hotel to give us relaxation massages. Although usually they come to our home, where we focus on pain related issues. We will continue to work with them for a long, long time.

Target Market(s)

Mobile massage therapy clients

Industry/Entity Type

Massage Therapy

Coding

Coded - Design and coding required

Number of Pages Required

1 page

Font styles to use
Serif
Sans Serif

Requirements
Must have
• Please add or remove any information that would help the presentation of our website. Our logo is posted below, please include into the website.
• Please include a contact field that includes, kestrelwaymassage@fernmail.net,
• (206) 555-0148
• We have also included our own stock photos, as well as a photo of Paul and Lina. Please include a cropped photo of both massage therapists.

```html
<!DOCTYPE html>
<html lang="en">
<head>
<meta charset="utf-8">
<title>Kestrel Way Mobile Massage</title>
<link href="https://fonts.googleapis.com/css2?family=Roboto:ital,wght@0,300;0,400;0,500;0,700;1,400&display=swap" rel="stylesheet">
<style>
:root{
  --brand:#1a9ad6;
  --brand-dark:#156fae;
  --navy:#17203b;
  --ink:#3d4a5c;
  --muted:#7b8594;
  --line:#e3e7ec;
  --paper:#ffffff;
  --stone:#dcdfe3;
  --slate:#8d949c;
}
*{box-sizing:border-box;margin:0;padding:0}
html,body{width:695px;height:1200px;overflow:hidden}
body{font-family:"Roboto",Arial,sans-serif;color:var(--ink);background:var(--paper);position:relative}

.site-header{height:70px;position:relative;border-bottom:3px solid var(--brand)}
.brand{position:absolute;left:24px;top:6px;display:flex;align-items:center;gap:8px}
.brand-dot{width:56px;height:56px;border-radius:50%;background:var(--brand-dark)}
.brand-name{font-size:15px;font-weight:700;color:var(--brand-dark)}
.call{position:absolute;right:24px;top:12px;text-align:right;font-size:9px;color:var(--muted)}
.call strong{display:block;font-size:12px;color:var(--navy);font-weight:500}
.call svg{position:absolute;left:-18px;top:6px}
.main-nav{position:absolute;right:24px;top:50px;display:flex;gap:26px;font-size:8.5px;color:var(--muted)}
.main-nav .active{color:var(--navy);font-weight:500}

.hero{position:relative;height:275px;background:linear-gradient(110deg,#9aa4ad 0%,#c9ced2 35%,#6f7a84 70%,#3f4852 100%)}
.hero-tag{position:absolute;left:72px;top:88px;background:var(--brand-dark);color:#fff;font-size:17px;font-weight:400;padding:8px 14px}

.intro{height:175px;text-align:center;padding:28px 60px 0}
.intro h1{font-size:17px;font-weight:500;color:var(--navy);margin-bottom:12px}
.intro p{font-size:7.5px;line-height:1.5;color:var(--muted);text-align:left}
.btn-outline{display:inline-block;margin-top:16px;border:1px solid #b9c0c8;font-size:8px;padding:7px 16px;color:var(--ink)}

.split{display:flex;height:190px}
.split-panel{flex:1;padding:26px 32px 0;position:relative}
.split-panel.passion{background:linear-gradient(120deg,#eceef0,var(--stone))}
.split-panel.education{background:linear-gradient(120deg,var(--slate),#6b737c);color:#fff}
.split-panel h2{font-size:19px;font-weight:500;color:var(--brand-dark);margin-bottom:8px}
.split-panel.education h2{color:#fff}
.split-panel p{font-size:6.6px;line-height:1.45}
.split-panel .btn-small{display:inline-block;margin-top:10px;font-size:7px;padding:5px 11px;border:1px solid currentColor}

.rates{padding:26px 50px 0;height:170px;text-align:center}
.rates h2{font-size:19px;font-weight:500;color:var(--brand-dark);margin-bottom:18px}
.rate-list{display:flex;gap:34px}
.rate-card{flex:1;height:56px;background:var(--brand);color:#fff;display:flex;align-items:center;padding:0 12px;text-align:left}
.rate-price{font-size:27px;font-weight:500;line-height:1}
.rate-time{font-size:7px;display:block;margin-top:2px}
.rate-book{margin-left:auto;font-size:6.5px;border:1px solid rgba(255,255,255,.7);padding:5px 6px}

.testimonial{position:relative;margin:0 76px;height:84px;border:1px solid var(--line);padding:14px 34px 0;text-align:center}
.testimonial blockquote{font-size:8px;line-height:1.55;font-style:italic;color:var(--muted)}
.testimonial cite{font-weight:700;font-style:normal;color:var(--ink)}
.testimonial .quote-mark{position:absolute;left:50%;bottom:-11px;margin-left:-11px;width:22px;height:22px;border-radius:50%;background:#fff;border:1px solid var(--line)}

.contact{position:absolute;left:0;top:990px;width:695px;height:170px;background:linear-gradient(135deg,#1e4ea3,#2d6fd0 55%,#1b3f8e);text-align:center;padding-top:40px}
.contact h2{font-size:15px;font-weight:500;color:#fff;margin-bottom:12px}
.form{width:460px;margin:0 auto}
.form-row{display:flex;gap:8px;margin-bottom:7px}
.field{flex:1;height:14px;background:#fff;font-size:6px;color:#9aa2ab;text-align:left;padding:3px 5px}
.field.message{height:20px}
.submit{display:inline-block;background:var(--brand);color:#fff;font-size:7px;padding:4px 10px}

.site-footer{position:absolute;left:0;top:1160px;width:695px;height:40px;background:var(--navy);color:#a6adbb;display:flex;align-items:center;padding:0 28px;font-size:6.5px;gap:10px}
.footer-dot{width:22px;height:22px;border-radius:50%;background:var(--brand-dark)}
.footer-text strong{color:#fff;font-weight:500}
.social{margin-left:auto;display:flex;gap:6px}
.social span{width:14px;height:14px;border-radius:50%;background:var(--brand)}
</style>
</head>
<body>

<header class="site-header">
  <div class="brand"><span class="brand-dot"></span><span class="brand-name">Kestrel Way</span></div>
  <div class="call">
    <svg width="12" height="12" viewBox="0 0 24 24"><path d="M6.6 10.8a15 15 0 006.6 6.6l2.2-2.2c.3-.3.7-.4 1-.2 1.1.4 2.3.6 3.6.6.6 0 1 .4 1 1V20c0 .6-.4 1-1 1A17 17 0 013 4c0-.6.4-1 1-1h3.5c.6 0 1 .4 1 1 0 1.3.2 2.5.6 3.6.1.3 0 .7-.2 1z" fill="#1a9ad6"/></svg>
    Call Us
    <strong>(206) 555-0148</strong>
  </div>
  <nav class="main-nav">
    <span class="active">Why we stand out</span><span>Our passion</span><span>Our education</span><span>Our rates</span><span>Contact us</span>
  </nav>
</header>

<section class="hero" role="img" aria-label="Therapist giving a massage to a client in a bright living room">
  <div class="hero-tag">We are a male and female<br>mobile massage team</div>
</section>

<section class="intro">
  <h1>Kestrel Way is a Seattle based mobile massage service</h1>
  <p>Our massage is offered to the community with a goal of facilitating balance within each individual. We specialize in integrated Pain management, and sports/medical massage therapy. Every client's first assessment is attended by our male and female massage therapist team. Depending on the goals identified for an individual determines which therapist will be assigned to provide treatment, if not both.</p>
  <span class="btn-outline">Book an appointment</span>
</section>

<section class="split">
  <div class="split-panel passion" role="img" aria-label="Soft photo of a massage treatment">
    <h2>Our Passion</h2>
    <p>Here at Kestrel Way, we have a great passion for Postural Restoration and how it is integrated into an individual's Massage treatment. We pride ourselves in being natural facilitators of healing, which takes the ego of the therapist out of the client's healing process. We strive to deliver the best massage possible by including modalities such as Neuromuscular, Myofascial release, spontaneous muscle release, postural restoration, orthopedic, and medical massage.</p>
    <span class="btn-small">Read more</span>
  </div>
  <div class="split-panel education" role="img" aria-label="Muted photo of a therapist at work">
    <h2>Our Education</h2>
    <p>We are both Graduates of Venmora, school of massage therapy. We have continuing education in medical massage, myofascial release, trigger point therapy, postural restoration, anatomy, and spontaneous muscle release. One of us is also a Certified Yoga Instructor, which amplifies experience with flexibility and strength as it pertains to each individual. The other brings massage, stretching, and strength training to encourage postural restoration and realignment.</p>
    <span class="btn-small">Read more</span>
  </div>
</section>

<section class="rates">
  <h2>Our Rates</h2>
  <div class="rate-list">
    <div class="rate-card"><div><span class="rate-price">$75</span><span class="rate-time">For 60 minutes</span></div><span class="rate-book">Book now</span></div>
    <div class="rate-card"><div><span class="rate-price">$95</span><span class="rate-time">For 90 minutes</span></div><span class="rate-book">Book now</span></div>
    <div class="rate-card"><div><span class="rate-price">$120</span><span class="rate-time">For 120 minutes</span></div><span class="rate-book">Book now</span></div>
  </div>
</section>

<section class="testimonial">
  <blockquote>" Phasellus nisl est, condimentum vitae faucibus in, sollicitudin vel metus. Nunc sit amet consequat risus. Curabitur eu elit leo. In eleifend dui tellus, in scelerisque elit porttitor et. Integer eu massa lacus, lacinia nulla non, volutpat purus. Sed libero felis, vestibulum vel dolor eget, lacinia aliquet neque." <cite>- Marcus Hale, City</cite></blockquote>
  <span class="quote-mark"></span>
</section>

<section class="contact">
  <h2>Make a Quick Contact</h2>
  <div class="form">
    <div class="form-row"><span class="field">Name</span><span class="field">Email</span><span class="field">Phone</span><span class="field">Subject</span></div>
    <div class="form-row"><span class="field message">Message</span></div>
    <span class="submit">Submit</span>
  </div>
</section>

<footer class="site-footer">
  <span class="footer-dot"></span>
  <div class="footer-text"><strong>Kestrel Way Massage</strong> | kestrelwaymassage@fernmail.net | (206) 555-0148<br>Copyright © 2024 Kestrel Way. All rights reserved.</div>
  <div class="social"><span></span><span></span><span></span></div>
</footer>

</body>
</html>
```